Wordpress Design Project (Brindlow)

We need a wordpress design for an established auction and real estate company based in New Jersey. The winning design will incorporate a professional color scheme and company logo in a clean layout.

Industry/Entity Type

Real Estate

Requirements
Must have
• - We will require winning designer to provide a layered PSD (Adobe photoshop) concept file, along with any non-standard font files used.

Logo attached. Will hopefully post better logo shortly. Please use site design colors of your choice as the logo is black & white. A site client mentions liking is http://www.qelmarbidding.example/. Homepage content will be an auction list as seen at http://www.gavelroundup.example/?page=5

Horizontal Navigation menu with these pages:
Home - Auction Calendar - Appraisals - Services - Company Profile - News & Events - Testimonials - Contact Us

A slideshow element on the home page using one of the placeholder images provided (or stock if higher resolution image is necessary).

Sidebar widgets to be included are: Email sign-up form - Featured Auctions - Testimonial widget - 'Our Videos' widget; Social media icons somewhere in layout (facebook, twitter, RSS, and Youtube)

Homepage content is text:
BRINDLOW MANAGEMENT COMPANY was founded 90 years ago in 1921 by Harold Brindlow, which makes us one of the oldest commercial and industrial auction and appraisal companies in America.

We have conducted thousands of auctions, assisting a wide range of companies both large and small achieve maximum value for their capital assets.
Nice to have
• - Site will have drop down menus, nice to have a sample look for them on one of the primary menu items.

```html
<!DOCTYPE html>
<html lang="en">
<head>
<meta charset="utf-8">
<title>Brindlow Auctioneers &amp; Appraisers</title>
<link href="https://fonts.googleapis.com/css2?family=Ubuntu:wght@400;500;700&family=Arimo:ital,wght@0,400;0,700;1,400&display=swap" rel="stylesheet">
<style>
:root{
  --red:#d5163b;
  --red-dark:#a80f2c;
  --ink:#2b2b2b;
  --text:#333333;
  --page:#efefef;
  --panel:#ffffff;
  --dark:#2a2a2a;
  --footer:#2b2b2b;
  --field:#ececec;
}
*{box-sizing:border-box;margin:0;padding:0}
html,body{width:993px;height:1200px;overflow:hidden;background:var(--page)}
body{font-family:"Arimo",Arial,sans-serif;color:var(--text)}
.stage{position:absolute;left:0;top:0;width:1200px;height:1450px;transform:scale(0.8275);transform-origin:0 0;background:var(--page);border-top:3px solid var(--red)}
.abs{position:absolute}

/* header */
.brand{left:118px;top:34px;display:flex;align-items:center;gap:12px}
.brand-mark{width:40px;height:40px;background:var(--ink)}
.brand-name{font-family:"Ubuntu",sans-serif;font-weight:700;font-size:36px;color:var(--ink);letter-spacing:1px}
.phone{left:893px;top:70px;display:flex;align-items:center;gap:10px}
.phone-icon{width:26px;height:26px;border-radius:5px;background:var(--red);display:flex;align-items:center;justify-content:center}
.phone-number{font-family:"Ubuntu",sans-serif;font-weight:700;font-size:24px;color:var(--ink)}

/* navigation */
.main-nav{left:102px;top:116px;width:996px;height:45px;background:var(--red);border-radius:6px;border:2px solid var(--red-dark);list-style:none}
.main-nav li{position:absolute;top:0;height:41px;display:flex;align-items:center;color:#fff;font-size:14.5px;white-space:nowrap}
.main-nav li.active{background:var(--dark);width:149px;padding-left:21px}
.dropdown{left:218px;top:163px;width:170px;height:67px;background:var(--dark);border:2px solid #444;padding:6px 8px;list-style:none}
.dropdown li{color:#fff;font-size:12.5px;height:23px;display:flex;align-items:center;padding-left:8px;margin-bottom:2px}
.dropdown li.current{background:var(--red);border:1px solid #ff6b84}
.dropdown-caret{left:244px;top:153px;width:0;height:0;border-left:9px solid transparent;border-right:9px solid transparent;border-bottom:10px solid var(--dark)}

/* panels */
.panel{background:var(--panel);border-radius:12px;box-shadow:0 1px 4px rgba(0,0,0,.08)}
.slider{left:104px;top:187px;width:660px;height:368px}
.slide-photo{left:115px;top:197px;width:639px;height:348px;border-radius:4px;background:linear-gradient(180deg,#9ec3e6 0%,#c9dcec 30%,#c0394a 45%,#d8243c 62%,#8d1a25 78%,#9a9a9a 100%)}
.slide-caption{left:115px;top:485px;width:639px;height:60px;background:rgba(30,30,30,.72);color:#fff;font-size:12.5px;line-height:22px;padding:4px 9px;border-radius:0 0 4px 4px}
.slide-caption strong{color:var(--red);font-weight:400}
.slide-arrow{top:325px;width:26px;height:67px;background:rgba(30,30,30,.8);display:flex;align-items:center;justify-content:center}

.signup{left:788px;top:185px;width:312px;height:366px}
.widget-title-red{font-family:"Ubuntu",sans-serif;font-weight:500;font-size:25px;color:var(--red)}
.signup-intro{font-size:12.5px;line-height:18px;letter-spacing:.6px;color:var(--text)}
.field{left:803px;width:282px;height:43px;border-radius:22px;background:var(--field);border:2px solid #dcdcdc;box-shadow:inset 0 2px 3px rgba(0,0,0,.08);font-size:13.5px;color:#444;display:flex;align-items:center;padding-left:18px}
.btn-subscribe{left:930px;top:494px;width:152px;height:44px;border-radius:12px;background:var(--red);border:2px solid #f06a83;color:#fff;font-family:"Ubuntu",sans-serif;font-size:17px;letter-spacing:.5px;display:flex;align-items:center;justify-content:center}

.video{left:788px;top:589px;width:312px;height:247px}
.video-screen{left:797px;top:600px;width:290px;height:222px;background:#000;border:1px solid #333}
.video-controls{left:797px;top:804px;width:290px;height:18px;background:#1d1d1d}
.video-shadow{left:840px;top:843px;width:215px;height:10px;border-radius:50%;background:radial-gradient(ellipse at center,rgba(0,0,0,.22),rgba(0,0,0,0) 70%)}

.featured-widget{left:788px;top:880px;width:312px;height:228px}
.widget-title{font-family:"Ubuntu",sans-serif;font-weight:500;font-size:21px;color:var(--ink)}
.featured-link{left:812px;top:932px;font-size:12.5px;color:var(--red);text-decoration:underline;letter-spacing:.8px}
.featured-text{left:812px;top:976px;width:130px;font-size:12px;line-height:14px;color:#111}
.featured-photo{left:956px;top:963px;width:124px;height:128px;background:linear-gradient(160deg,#3a3a3a,#1c1c1c 60%,#c8763f 85%,#e4b38a)}
.btn-readmore{left:824px;top:1069px;width:93px;height:26px;border-radius:13px;background:linear-gradient(#3a2a2a,#1a0e0e);color:#fff;font-style:italic;font-size:12.5px;display:flex;align-items:center;justify-content:center}

.testimonial-widget{left:788px;top:1135px;width:312px;height:178px}
.testimonial-text{left:808px;top:1185px;width:277px;font-size:12.3px;line-height:20px;text-align:justify;color:#222}

/* auctions */
.section-title{left:118px;top:589px;font-family:"Ubuntu",sans-serif;font-weight:500;font-size:20px;letter-spacing:1px;color:var(--ink);text-transform:uppercase}
.auction{left:0;width:770px;height:180px}
.auction-title{position:absolute;font-size:14.5px;font-weight:700;color:var(--red);letter-spacing:.7px;white-space:nowrap}
.auction-thumb{position:absolute;width:142px;height:95px;border:3px solid #fff;box-shadow:0 0 2px rgba(0,0,0,.3);background:linear-gradient(135deg,#8b8f86,#cfcfc5 45%,#6e7169 70%,#b9b6a8)}
.auction-body{position:absolute;font-size:12.5px;color:#222;font-style:italic;line-height:14px}
.auction-kind{font-family:"Ubuntu",sans-serif;font-style:normal;font-weight:500;font-size:14px;letter-spacing:1.3px;color:#6a5a4a;margin-bottom:9px}
.auction-body b{font-weight:700}
.auction-body p{margin-bottom:7px}
.btn{position:absolute;width:123px;height:27px;border-radius:14px;display:flex;align-items:center;gap:10px;padding-left:14px;color:#fff;font-size:13px}
.btn-red{background:var(--red);border:2px solid #f27a90}
.btn-dark{background:linear-gradient(#3b2c2c,#190d0d);border:2px solid #555}
.divider{left:104px;width:660px;border-top:1px dotted #ccc}

/* footer */
.site-footer{left:0;top:1357px;width:1200px;height:93px;background:var(--footer)}
.footer-brand{left:116px;top:1386px;display:flex;align-items:center;gap:12px}
.footer-brand .brand-mark{background:#fff}
.footer-brand .brand-name{color:#fff}
.copyright{left:517px;top:1403px;color:#fff;font-size:13.5px}
.social{top:1388px;width:36px;height:36px;border-radius:50%}
</style>
</head>
<body>
<div class="stage">

  <header>
    <div class="abs brand"><span class="brand-mark"></span><span class="brand-name">Brindlow</span></div>
    <div class="abs phone">
      <span class="phone-icon">
        <svg width="16" height="16" viewBox="0 0 24 24"><path fill="#fff" d="M6.6 10.8a15.1 15.1 0 0 0 6.6 6.6l2.2-2.2c.3-.3.7-.4 1-.2 1.1.4 2.3.6 3.6.6.6 0 1 .4 1 1V20c0 .6-.4 1-1 1A17 17 0 0 1 3 4c0-.6.4-1 1-1h3.5c.6 0 1 .4 1 1 0 1.3.2 2.5.6 3.6.1.3 0 .7-.2 1z"/></svg>
      </span>
      <span class="phone-number">555-018-4420</span>
    </div>
  </header>

  <ul class="abs main-nav">
    <li style="left:17px">Home</li>
    <li class="active" style="left:81px">Auction Calendar</li>
    <li style="left:259px">Appraisals</li>
    <li style="left:375px">Services</li>
    <li style="left:478px">Company Profile</li>
    <li style="left:632px">News &amp; Events</li>
    <li style="left:777px">Testimonials</li>
    <li style="left:904px">Contact Us</li>
  </ul>

  <!-- hero slideshow -->
  <div class="abs panel slider"></div>
  <div class="abs slide-photo" role="img" aria-label="Row of red semi-trucks parked outside the auction yard"></div>
  <div class="abs slide-caption"><strong>BRINDLOW MANAGEMENT COMPANY</strong> was founded 90 years ago in 1921 by Harold Brindlow, which makes us one of the oldest commercial and industrial auction and appraisal companies in America.</div>
  <div class="abs slide-arrow" style="left:115px"><svg width="12" height="22" viewBox="0 0 12 22"><path d="M10 2 2 11l8 9" fill="none" stroke="#fff" stroke-width="3"/></svg></div>
  <div class="abs slide-arrow" style="left:728px"><svg width="12" height="22" viewBox="0 0 12 22"><path d="M2 2l8 9-8 9" fill="none" stroke="#fff" stroke-width="3"/></svg></div>

  <div class="abs dropdown-caret"></div>
  <ul class="abs dropdown">
    <li class="current">About Halvorsen</li>
    <li>Testimonials</li>
  </ul>

  <!-- sidebar: signup -->
  <div class="abs panel signup"></div>
  <h2 class="abs widget-title-red" style="left:801px;top:210px">Email sign-up form</h2>
  <p class="abs signup-intro" style="left:803px;top:251px;width:280px">Lorem ipsum dolor sit amet, consectetuer adipiscing elit. Nam</p>
  <div class="abs field" style="top:315px">First Name</div>
  <div class="abs field" style="top:371px">Last Name</div>
  <div class="abs field" style="top:427px">Email Address</div>
  <div class="abs btn-subscribe">Subscribe Now</div>

  <!-- main: featured auctions -->
  <h2 class="abs section-title">Featured Auctions</h2>

  <article class="abs auction" style="top:626px">
    <h3 class="auction-title" style="left:126px;top:0">2005 RIDGEWAY SUMMIT 34-FT. CAMPER</h3>
    <div class="auction-thumb" style="left:119px;top:29px" role="img" aria-label="Industrial printing press machinery"></div>
    <div class="auction-body" style="left:271px;top:29px">
      <div class="auction-kind">LIVE ON-SITE AUCTION</div>
      <p><b>Begins:</b>&nbsp; Tuesday, April 23, 2013 at 10:00 AM EDT</p>
      <p style="margin-top:13px"><b>Location:</b>&nbsp; Harbor Ridge Entrance- 4100 W. Orchard Hwy 9<br>Harbor Ridge Rd (Auction Property)<br>Pine Hollow, FL 33000</p>
    </div>
    <div class="btn btn-red" style="left:125px;top:143px"><svg width="14" height="14" viewBox="0 0 14 14" fill="#fff"><rect x="0" y="0" width="3" height="3"/><rect x="0" y="5.5" width="3" height="3"/><rect x="0" y="11" width="3" height="3"/><rect x="5" y="1" width="9" height="1.5"/><rect x="5" y="6.3" width="9" height="1.5"/><rect x="5" y="11.6" width="9" height="1.5"/></svg>Details Now</div>
    <div class="btn btn-dark" style="left:269px;top:143px"><svg width="15" height="13" viewBox="0 0 15 13"><rect x="1" y="1" width="13" height="11" fill="none" stroke="#fff" stroke-width="1.5"/><path d="M3 10l3-4 2 2 2-3 3 5z" fill="#fff"/></svg>Details Now</div>
  </article>
  <div class="abs divider" style="top:829px"></div>

  <article class="abs auction" style="top:865px">
    <h3 class="auction-title" style="left:116px;top:0">Sells to the Highest Bidder! 1+ Acre Real Estate Auction Pleasant Plain.</h3>
    <div class="auction-thumb" style="left:119px;top:41px" role="img" aria-label="Industrial printing press machinery"></div>
    <div class="auction-body" style="left:271px;top:39px">
      <div class="auction-kind">LIVE ON-SITE AUCTION</div>
      <p><b>Begins:</b>&nbsp; Tuesday, April 23, 2013 at 10:00 AM EDT</p>
      <p style="margin-top:13px"><b>Location:</b>&nbsp; Harbor Ridge Entrance- 4100 W. Orchard Hwy 9<br>Harbor Ridge Rd (Auction Property)<br>Pine Hollow, FL 33000</p>
    </div>
    <div class="btn btn-red" style="left:125px;top:153px"><svg width="14" height="14" viewBox="0 0 14 14" fill="#fff"><rect x="0" y="0" width="3" height="3"/><rect x="0" y="5.5" width="3" height="3"/><rect x="0" y="11" width="3" height="3"/><rect x="5" y="1" width="9" height="1.5"/><rect x="5" y="6.3" width="9" height="1.5"/><rect x="5" y="11.6" width="9" height="1.5"/></svg>Details Now</div>
    <div class="btn btn-dark" style="left:269px;top:153px"><svg width="15" height="13" viewBox="0 0 15 13"><rect x="1" y="1" width="13" height="11" fill="none" stroke="#fff" stroke-width="1.5"/><path d="M3 10l3-4 2 2 2-3 3 5z" fill="#fff"/></svg>Details Now</div>
  </article>
  <div class="abs divider" style="top:1083px"></div>

  <article class="abs auction" style="top:1119px">
    <h3 class="auction-title" style="left:119px;top:0">Sells to the Highest Bidder! 1+ Acre Real Estate Auction Pleasant Plain.</h3>
    <div class="auction-thumb" style="left:120px;top:40px" role="img" aria-label="Industrial printing press machinery"></div>
    <div class="auction-body" style="left:274px;top:39px">
      <div class="auction-kind">LIVE ON-SITE AUCTION</div>
      <p><b>Begins:</b>&nbsp; Tuesday, April 23, 2013 at 10:00 AM EDT</p>
      <p style="margin-top:13px"><b>Location:</b>&nbsp; Harbor Ridge Entrance- 4100 W. Orchard Hwy 9<br>Harbor Ridge Rd (Auction Property)<br>Pine Hollow, FL 33000</p>
    </div>
    <div class="btn btn-red" style="left:128px;top:153px"><svg width="14" height="14" viewBox="0 0 14 14" fill="#fff"><rect x="0" y="0" width="3" height="3"/><rect x="0" y="5.5" width="3" height="3"/><rect x="0" y="11" width="3" height="3"/><rect x="5" y="1" width="9" height="1.5"/><rect x="5" y="6.3" width="9" height="1.5"/><rect x="5" y="11.6" width="9" height="1.5"/></svg>Details Now</div>
    <div class="btn btn-dark" style="left:272px;top:153px"><svg width="15" height="13" viewBox="0 0 15 13"><rect x="1" y="1" width="13" height="11" fill="none" stroke="#fff" stroke-width="1.5"/><path d="M3 10l3-4 2 2 2-3 3 5z" fill="#fff"/></svg>Details Now</div>
  </article>

  <!-- sidebar: video -->
  <div class="abs panel video"></div>
  <div class="abs video-screen"></div>
  <svg class="abs" style="left:926px;top:686px" width="34" height="34" viewBox="0 0 34 34"><circle cx="17" cy="17" r="15" fill="none" stroke="#fff" stroke-width="3"/><path d="M13 10l11 7-11 7z" fill="#fff"/></svg>
  <div class="abs video-controls">
    <svg width="290" height="18" viewBox="0 0 290 18"><circle cx="11" cy="9" r="5" fill="none" stroke="#ddd" stroke-width="1.5"/><path d="M9.5 6.5l4 2.5-4 2.5z" fill="#ddd"/><rect x="22" y="8" width="170" height="2" fill="#555"/><rect x="256" y="8" width="16" height="2" fill="#ccc"/></svg>
  </div>
  <div class="abs video-shadow"></div>

  <!-- sidebar: featured auctions -->
  <div class="abs panel featured-widget"></div>
  <h2 class="abs widget-title" style="left:810px;top:891px">Featured Auctions</h2>
  <a class="abs featured-link">TRACTOR * HI LIFT * MACHINERY</a>
  <p class="abs featured-text"><b>Saturday</b> March 16, 2013 at 10:00 AM<br><span style="display:block;margin-top:7px">simply dummy text of the printing and type-setting industry.</span></p>
  <div class="abs featured-photo" role="img" aria-label="Hands holding a small model house"></div>
  <div class="abs btn-readmore">Read more</div>

  <!-- sidebar: testimonials -->
  <div class="abs panel testimonial-widget"></div>
  <h2 class="abs widget-title" style="left:807px;top:1150px">Testimonials</h2>
  <p class="abs testimonial-text">simply dummy text of the printing and typesetting industry. Lorem Ipsum has been the industry's standard dummy text ever since the 1500s, when an unknown printer took a galley of type and scrambled it to make a type specimen book.</p>

  <!-- footer -->
  <footer class="abs site-footer"></footer>
  <div class="abs footer-brand"><span class="brand-mark"></span><span class="brand-name">Brindlow</span></div>
  <p class="abs copyright">Copyright © Brindlow &amp; Auctioneers.</p>
  <span class="abs social" style="left:903px;background:#3b5b98" aria-label="Social profile link"></span>
  <span class="abs social" style="left:951px;background:#2aa4d8" aria-label="Social profile link"></span>
  <span class="abs social" style="left:998px;background:#e8661c" aria-label="News feed link"></span>
  <span class="abs social" style="left:1045px;background:#e6e6e6" aria-label="Video channel link"></span>

</div>
</body>
</html>
```